Landscape design build company door flyer

I would like this flyer to convey a high-level of professionalism for a company that is excellent with communication with their clients as well as a company that does incredible installations

Went on vacation/holiday

```html
<!DOCTYPE html>
<html lang="en">
<head>
<meta charset="utf-8">
<title>Cedar Stone Builders – Outdoor Living Spaces Flyer</title>
<link rel="stylesheet" href="https://fonts.googleapis.com/css2?family=Rubik:wght@700&family=Roboto+Condensed:wght@400;700&family=Roboto:wght@500;700&display=swap">
<style>
  :root{
    --navy:#0f2b40;
    --white:#ffffff;
    --paper-grey:#e7e7e8;
    --backdrop:#ececec;
    --muted:#c7cbd0;
    --text:#1d2730;
  }
  *{box-sizing:border-box;margin:0;padding:0}
  html,body{width:1200px;height:1029px;overflow:hidden;background:var(--backdrop)}
  .flyer{
    position:absolute;left:227px;top:34px;width:1228px;height:1580px;
    transform:scale(.6076);transform-origin:0 0;
    background:var(--white);overflow:hidden;
    box-shadow:0 6px 40px rgba(0,0,0,.18);
    font-family:"Roboto Condensed",sans-serif;color:var(--text);
  }
  .hero-photo{
    position:absolute;left:0;top:0;width:1228px;height:622px;
    background:linear-gradient(100deg,#3f5a33 0%,#6d7064 22%,#5b5c5f 45%,#6e7076 60%,#4f5a4c 78%,#8fb3c9 100%);
  }
  .hero-split{position:absolute;left:612px;top:195px;width:5px;height:190px;background:var(--white)}
  .headline-banner{position:absolute;left:0;top:0;width:1228px;height:200px}
  .headline{
    position:absolute;left:0;top:38px;width:1228px;text-align:center;
    font-family:"Rubik",sans-serif;font-weight:700;font-size:56px;line-height:72px;
    color:var(--white);letter-spacing:.5px;
  }
  .brand{position:absolute;left:0;top:645px;width:1228px;text-align:center;color:var(--navy)}
  .brand-name{font-family:"Roboto Condensed",sans-serif;font-weight:700;font-size:66px;line-height:76px;letter-spacing:1px}
  .brand-tagline{font-family:"Roboto Condensed",sans-serif;font-weight:700;font-size:31px;line-height:34px;letter-spacing:.5px}
  .intro{position:absolute;left:69px;top:814px;width:580px;font-size:27px;line-height:35px}
  .services{position:absolute;left:69px;top:968px;width:620px;display:grid;grid-template-columns:289px 330px;row-gap:22px;list-style:none}
  .service{display:flex;align-items:center;gap:14px;font-family:"Roboto",sans-serif;font-weight:500;font-size:23px;height:44px;color:var(--text)}
  .service svg{width:44px;height:44px;flex:none}
  .gallery{position:absolute;left:0;top:700px;width:1228px;height:780px}
  .contact-band{position:absolute;left:0;top:0;width:1228px;height:1580px}
  .service-areas{position:absolute;left:69px;top:1298px;width:600px;color:var(--white);font-size:25px;line-height:30px}
  .cta{position:absolute;left:69px;top:1370px;color:var(--muted);font-weight:700;font-size:46px;line-height:54px}
  .phone{position:absolute;left:69px;top:1432px;display:flex;align-items:center;gap:22px;color:var(--white);font-family:"Roboto",sans-serif;font-weight:700;font-size:74px;line-height:90px}
  .phone svg{width:78px;height:78px}
  .link{position:absolute;left:792px;display:flex;align-items:center;gap:18px;font-weight:700;font-size:31px}
  .link svg{width:40px;height:40px}
  .link-email{top:1403px;color:var(--white)}
  .link-web{top:1504px;color:var(--navy)}
</style>
</head>
<body>
<main class="flyer">
  <div class="hero-photo" role="img" aria-label="Photo of a covered stone patio with stacked-stone bar counters, timber posts and paver floor"></div>
  <div class="hero-split"></div>

  <svg class="headline-banner" viewBox="0 0 1228 200" aria-hidden="true">
    <polygon points="168,0 1062,0 960,198 282,198" fill="#ffffff"/>
    <polygon points="176,0 1054,0 955,192 288,192" fill="var(--navy)"/>
  </svg>
  <h1 class="headline">DO YOU NEED A TRUSTED<br>BUILDING CONTRATOR?</h1>

  <div class="brand">
    <div class="brand-name">CEDAR STONE BUILDERS</div>
    <div class="brand-tagline">OUTDOOR LIVING SPACES</div>
  </div>

  <p class="intro">At Cedar Stone Builders, our passion is to go above and beyond to craft amazing outdoor environments for clients. Our services are:</p>

  <ul class="services">
    <li class="service"><svg viewBox="0 0 44 44"><path d="M3 42V15L22 3l19 12v27" fill="none" stroke="var(--navy)" stroke-width="2.5"/><path d="M13 30h18M16 30v8M28 30v8M22 17v13M14 21h16" stroke="var(--navy)" stroke-width="2.5" fill="none"/></svg>Paver Patios</li>
    <li class="service"><svg viewBox="0 0 44 44"><path d="M3 42V15L22 3l19 12v27" fill="none" stroke="var(--navy)" stroke-width="2.5"/><rect x="12" y="20" width="20" height="16" fill="none" stroke="var(--navy)" stroke-width="2.5"/><path d="M12 26h20M12 31h20" stroke="var(--navy)" stroke-width="2"/></svg>Decks &amp; Railings</li>
    <li class="service"><svg viewBox="0 0 44 44"><path d="M3 42V15L22 3l19 12v27" fill="none" stroke="var(--navy)" stroke-width="2.5"/><path d="M9 33l8-10h10l8 10z" fill="var(--navy)"/></svg>Paver Driveways</li>
    <li class="service"><svg viewBox="0 0 44 44"><path d="M3 42V15L22 3l19 12v27" fill="none" stroke="var(--navy)" stroke-width="2.5"/><path d="M14 32V24l8-6 8 6v8h-5v-5h-6v5z" fill="var(--navy)"/></svg>Firepits &amp; Fireplaces</li>
    <li class="service"><svg viewBox="0 0 44 44"><path d="M3 42V15L22 3l19 12v27" fill="none" stroke="var(--navy)" stroke-width="2.5"/><path d="M12 18h12v5H12zM16 23h12v5H16zM20 28h12v5H20z" fill="var(--navy)"/></svg>Retaining Walls</li>
    <li class="service"><svg viewBox="0 0 44 44"><path d="M3 42V15L22 3l19 12v27" fill="none" stroke="var(--navy)" stroke-width="2.5"/><path d="M18 18h8l-2 10h-4zM22 28v8M18 36h8" fill="none" stroke="var(--navy)" stroke-width="2.5"/></svg>Outdoor Lighting</li>
    <li class="service"><svg viewBox="0 0 44 44"><path d="M3 42V15L22 3l19 12v27" fill="none" stroke="var(--navy)" stroke-width="2.5"/><path d="M16 17v14M28 17v14M16 22h12M16 27h12M10 33c4-3 8 3 12 0s8 3 12 0M10 37c4-3 8 3 12 0s8 3 12 0" fill="none" stroke="var(--navy)" stroke-width="2"/></svg>Pools</li>
    <li class="service"><svg viewBox="0 0 44 44"><path d="M3 42V15L22 3l19 12v27" fill="none" stroke="var(--navy)" stroke-width="2.5"/><circle cx="22" cy="27" r="8" fill="none" stroke="var(--navy)" stroke-width="2"/><path d="M22 22v10M17 27h10" stroke="var(--navy)" stroke-width="2"/></svg>And More...</li>
  </ul>

  <svg class="contact-band" viewBox="0 0 1228 1580" aria-hidden="true">
    <rect x="0" y="1485" width="1228" height="95" fill="var(--paper-grey)"/>
    <polygon points="0,1280 642,1280 740,1365 1228,1365 1228,1485 760,1485 715,1552 0,1552" fill="var(--navy)"/>
  </svg>

  <svg class="gallery" viewBox="0 700 1228 780">
    <defs>
      <linearGradient id="aerial" x1="0" y1="0" x2="1" y2="1">
        <stop offset="0" stop-color="#4d6a3c"/><stop offset=".45" stop-color="#6f7a86"/><stop offset="1" stop-color="#5a4c42"/>
      </linearGradient>
      <linearGradient id="dusk" x1="0" y1="0" x2="0" y2="1">
        <stop offset="0" stop-color="#5f86c4"/><stop offset=".45" stop-color="#2f3f52"/><stop offset=".75" stop-color="#8a5a3a"/><stop offset="1" stop-color="#6b6f76"/>
      </linearGradient>
    </defs>
    <polygon points="1006,725 1296,893 1296,1228 1006,1395 716,1228 716,893" fill="var(--paper-grey)"/>
    <polygon points="1006,762 1266,912 1266,1210 1006,1360 746,1210 746,912" fill="var(--navy)"/>
    <polygon points="1006,798 1233,929 1233,1191 1006,1322 779,1191 779,929" fill="#ffffff"/>
    <g role="img" aria-label="Aerial photo of a house with a new paver driveway and planted beds">
      <polygon points="1006,810 1222,935 1222,1185 1006,1310 790,1185 790,935" fill="url(#aerial)"/>
    </g>
    <polygon points="822,1083 952,1158 952,1308 822,1383 692,1308 692,1158" fill="var(--paper-grey)"/>
    <polygon points="822,1097 940,1165 940,1301 822,1369 704,1301 704,1165" fill="var(--navy)"/>
    <polygon points="822,1110 928,1171 928,1295 822,1356 716,1295 716,1171" fill="#ffffff"/>
    <g role="img" aria-label="Photo of a lakeside fire pit patio with lounge chairs at dusk">
      <polygon points="822,1120 920,1177 920,1289 822,1346 724,1289 724,1177" fill="url(#dusk)"/>
    </g>
  </svg>

  <p class="service-areas">Our service areas includes Bellevue, Issaquah, Kirkland, Redmond, Sammamish.</p>
  <p class="cta">CONTACT US TODAY</p>
  <p class="phone"><svg viewBox="0 0 80 80" aria-hidden="true"><path d="M20 8l12 14-7 8c4 9 12 17 21 21l8-7 14 12-8 12C35 66 12 43 8 16z" fill="#fff"/><path d="M48 10a24 24 0 0 1 22 22M46 20a14 14 0 0 1 14 14" fill="none" stroke="#fff" stroke-width="5"/></svg>[555]-014-2290</p>

  <p class="link link-email"><svg viewBox="0 0 40 40" aria-hidden="true"><rect x="2" y="8" width="36" height="24" fill="#fff"/><path d="M2 8l18 14L38 8" fill="none" stroke="var(--navy)" stroke-width="3"/></svg>info@cedarstonebuilders.com</p>
  <p class="link link-web"><svg viewBox="0 0 40 40" aria-hidden="true"><circle cx="20" cy="20" r="16" fill="none" stroke="var(--navy)" stroke-width="2.5"/><ellipse cx="20" cy="20" rx="7" ry="16" fill="none" stroke="var(--navy)" stroke-width="2"/><path d="M4 20h32M7 12h26M7 28h26" stroke="var(--navy)" stroke-width="2"/></svg>www.cedarstonebuilders.com</p>
</main>
</body>
</html>
```